Thornbury Building Company - Card Design

I am looking to use the logo designs that you already did for me to develop a business card. I would like the card to have a black background and be double sided. I want white and green logo and text. I have attached an inspiration photo of a look that I like. I would like to use the Vertical Logo attached to take up the full front side of the card. On the back where I have my name and information, I would like to have the horizontal logo or maybe even just the image of the 'A' and trees without the text. I am open, but I am looking for something clean and simple and I want the green to really pop! Additional files can be found under Design #: 58302946

Target Market(s)

Homeowners

Industry/Entity Type

Construction

Contact Information for Business Card

Name: Marcus Thornbury, Title: Project Manager, Phone: 555.274.8136, Email: thornburybuildingcompany@mailvesta.com, address: 487 Larkspur Ln, Felton, CA 95033, Lic# 2468317

Colors
00AB8E
00BBA5
67D7C9
C6EFE9
E9F9F6

Requirements
Nice to have
• I would like to see the logos that I have already got from ArtLoomHub, though I am open to new ones

```html
<!DOCTYPE html>
<html lang="en">
<head>
<meta charset="utf-8">
<title>Thornbury Building Company – Business Card</title>
<link rel="stylesheet" href="https://fonts.googleapis.com/css2?family=Arimo:wght@400;700&display=swap">
<style>
  :root {
    --backdrop: #262626;
    --card: #1b1b1b;
    --card-edge: #232323;
    --green: #5cc83b;
    --white: #f2f2f2;
  }
  * { box-sizing: border-box; margin: 0; padding: 0; }
  html, body {
    width: 1200px; height: 801px; overflow: hidden;
    background: var(--backdrop);
    font-family: "Arimo", Arial, sans-serif;
  }
  .stage {
    width: 1200px; height: 801px;
    display: flex; align-items: center; justify-content: center; gap: 40px;
  }
  .card {
    position: relative;
    width: 540px; height: 309px;
    background: linear-gradient(160deg, var(--card-edge), var(--card) 60%);
    border-bottom: 3px solid var(--green);
    border-left: 2px solid var(--green);
    box-shadow: 0 14px 30px rgba(0,0,0,.55);
    overflow: hidden;
  }
  /* info side */
  .company-mark {
    position: absolute; top: 28px; right: 30px;
    display: flex; align-items: center; gap: 9px;
    color: var(--white); font-weight: 700; font-size: 15px; letter-spacing: 1.5px;
    text-transform: uppercase;
  }
  .company-mark .mark-square { width: 14px; height: 14px; background: var(--green); }
  .person { position: absolute; left: 34px; top: 122px; }
  .person-name {
    color: var(--green); font-weight: 700; font-size: 26px; letter-spacing: .5px;
    line-height: 30px;
  }
  .person-title { color: var(--white); font-size: 15px; margin-top: 4px; }
  .divider {
    position: absolute; left: 34px; right: 30px; top: 198px;
    height: 1px; background: var(--green);
  }
  .contact { position: absolute; left: 34px; top: 218px; list-style: none; }
  .contact li {
    display: flex; align-items: center; gap: 9px;
    color: var(--white); font-size: 14px; margin-bottom: 9px;
  }
  .contact svg { width: 13px; height: 13px; flex: none; }
  .office {
    position: absolute; right: 30px; top: 146px; text-align: right;
    font-size: 14px; line-height: 18px;
  }
  .office .licence { color: var(--green); }
  .office .address { color: var(--white); margin-top: 5px; }
  /* brand side */
  .brand-side { display: flex; align-items: center; justify-content: center; }
  .brand-name {
    color: var(--white); font-weight: 700; font-size: 30px; letter-spacing: 3px;
    text-transform: uppercase; text-align: center; line-height: 1.25;
  }
</style>
</head>
<body>
<main class="stage">
  <section class="card info-side" aria-label="Card back with contact details">
    <div class="company-mark"><span class="mark-square"></span>Thornbury Building Company</div>
    <div class="person">
      <h1 class="person-name">MARCUS THORNBURY</h1>
      <p class="person-title">Project Manager</p>
    </div>
    <div class="office">
      <p class="licence">Lic# 2468317</p>
      <p class="address">487 Larkspur Ln, Felton, CA 95033</p>
    </div>
    <div class="divider"></div>
    <ul class="contact">
      <li>
        <svg viewBox="0 0 24 24" aria-hidden="true"><path fill="#5cc83b" d="M6.6 10.8a15.1 15.1 0 0 0 6.6 6.6l2.2-2.2c.3-.3.7-.4 1-.2 1.1.4 2.3.6 3.6.6.6 0 1 .4 1 1V20c0 .6-.4 1-1 1A17 17 0 0 1 3 4c0-.6.4-1 1-1h3.5c.6 0 1 .4 1 1 0 1.3.2 2.5.6 3.6.1.3 0 .7-.2 1z"/></svg>
        555.274.8136
      </li>
      <li>
        <svg viewBox="0 0 24 24" aria-hidden="true"><path fill="#5cc83b" d="M2 5h20v14H2zm2 2v.5l8 5 8-5V7z"/></svg>
        thornburybuildingcompany@mailvesta.com
      </li>
    </ul>
  </section>

  <section class="card brand-side" aria-label="Card front with company name">
    <p class="brand-name">Thornbury<br>Building Company</p>
  </section>
</main>
</body>
</html>
```